New Business Card Design Project

We require a business card design for Vexalund, a newly established Indian company.
Our focus is on the development, manufacturing, and export of a diverse array of pharmaceutical products on a global scale. The card should convey a professional appearance, as our primary markets are in Africa, China, and Southeast Asian nations.
We envision a two-sided business card, with the reverse side dedicated to a logo set against a solid color or an elegantly designed pattern. The corners should be rounded. We would appreciate seeing both horizontal and vertical design options. We trust the designer to utilize their expertise in creating this design.

The content for the business card is included in the attached Word file.

Target Market(s)

Our primary markets are in Africa, China, and Southeast Asian, Latin America, Maldives, Sri Lanka

Industry/Entity Type

Pharmaceutical Manufacturing and Export

Contact Information for Business Card

Colors

Designer to choose colors to be used in the design.

Requirements
Must have
• The reverse side of the business card features solely the logo along with the tagline, "Healing for All."
Should not have
• The logo should not exceed two instances, encompassing both the front and back sides of the card.

```html
<!DOCTYPE html>
<html lang="en">
<head>
<meta charset="utf-8">
<title>Vexalund Business Card</title>
<link rel="stylesheet" href="https://fonts.googleapis.com/css2?family=Poppins:wght@300;400;700&family=Open+Sans:wght@400;600&display=swap">
<style>
  :root {
    --bg: #232324;
    --card: #1f1f22;
    --blue: #2ea6de;
    --coral: #f26552;
    --white: #f2f2f2;
    --line: #2b86b5;
  }
  * { margin: 0; padding: 0; box-sizing: border-box; }
  html, body { width: 1200px; height: 711px; overflow: hidden; background: var(--bg); }
  .canvas {
    position: relative; width: 1200px; height: 711px;
    display: flex; align-items: center; justify-content: center; gap: 40px;
  }
  .card {
    position: relative; width: 540px; height: 320px;
    background: var(--card); border-radius: 24px;
    border-bottom: 4px solid var(--blue);
    box-shadow: 0 10px 24px rgba(0,0,0,.55);
    overflow: hidden;
  }
  .brand-name {
    font-family: "Poppins", sans-serif; font-weight: 700;
    color: var(--blue); letter-spacing: .5px; line-height: 1;
    display: flex; align-items: center; gap: 12px;
    white-space: nowrap;
  }
  .brand-dot { width: .55em; height: .55em; border-radius: 50%; background: var(--coral); flex: none; }
  .card-back { display: flex; flex-direction: column; align-items: center; justify-content: center; }
  .card-back .brand-name { font-size: 54px; }
  .tagline {
    margin-top: 16px; font-family: "Poppins", sans-serif; font-weight: 400;
    font-size: 14px; color: var(--white); letter-spacing: .6px;
  }
  .card-front .brand-block {
    position: absolute; left: 0; top: 0; width: 270px; height: 250px;
    display: flex; align-items: center; justify-content: center;
  }
  .card-front .brand-name { font-size: 38px; }
  .divider {
    position: absolute; left: 280px; top: 50px; width: 1px; height: 160px; background: var(--line);
  }
  .contact-block { position: absolute; left: 310px; top: 52px; }
  .person-name { font-family: "Poppins", sans-serif; font-size: 24px; line-height: 1.1; white-space: nowrap; }
  .person-first { color: var(--blue); font-weight: 700; }
  .person-last { color: var(--coral); font-weight: 300; }
  .person-role {
    font-family: "Open Sans", sans-serif; font-size: 14px; color: var(--white); margin-top: 4px;
  }
  .contact-list { list-style: none; margin-top: 22px; }
  .contact-item {
    display: flex; align-items: center; gap: 10px; margin-bottom: 8px;
    font-family: "Open Sans", sans-serif; font-size: 13px; color: var(--white);
    white-space: nowrap;
  }
  .contact-icon { width: 14px; height: 14px; flex: none; }
  .address {
    position: absolute; left: 0; right: 0; bottom: 30px; text-align: center;
    font-family: "Open Sans", sans-serif; font-size: 13px; color: var(--white); letter-spacing: .3px;
  }
</style>
</head>
<body>
<main class="canvas">
  <section class="card card-back" aria-label="Card reverse side">
    <div class="brand-name"><span class="brand-dot"></span>Vexalund</div>
    <p class="tagline">Healing for All.</p>
  </section>

  <section class="card card-front" aria-label="Card front side">
    <div class="brand-block">
      <div class="brand-name"><span class="brand-dot"></span>Vexalund</div>
    </div>
    <div class="divider"></div>
    <div class="contact-block">
      <h1 class="person-name"><span class="person-first">Ravik</span> <span class="person-last">S. Tornel</span></h1>
      <p class="person-role">CEO</p>
      <ul class="contact-list">
        <li class="contact-item">
          <svg class="contact-icon" viewBox="0 0 14 14"><rect x="3" y="1" width="8" height="12" rx="1.5" fill="none" stroke="#f26552" stroke-width="1.5"/></svg>
          +91 90031 57248
        </li>
        <li class="contact-item">
          <svg class="contact-icon" viewBox="0 0 14 14"><circle cx="7" cy="7" r="5.5" fill="none" stroke="#2ea6de" stroke-width="1.4"/><ellipse cx="7" cy="7" rx="2.4" ry="5.5" fill="none" stroke="#2ea6de" stroke-width="1"/><line x1="1.5" y1="7" x2="12.5" y2="7" stroke="#2ea6de" stroke-width="1"/></svg>
          www.vexalund.com
        </li>
        <li class="contact-item">
          <svg class="contact-icon" viewBox="0 0 14 14"><rect x="1" y="3" width="12" height="8.5" rx="1" fill="none" stroke="#f26552" stroke-width="1.4"/><polyline points="1.5,3.5 7,8 12.5,3.5" fill="none" stroke="#f26552" stroke-width="1.2"/></svg>
          rtornel@vexalund.com
        </li>
      </ul>
    </div>
    <p class="address">12, Nilgiri Lane, Ambervale, 400100, India</p>
  </section>
</main>
</body>
</html>
```